Album cover for a single song to be released on Plunkora, Zelvar, Kindlomax etc.

- I wanted there to be silhouette figures dancing in a club with colors (maybe lights)
- I attached some examples I can also send more
- One of the silhouette should be a DJ
- The font for Morvanix should be done in the same style as a previous cover art In big blocky 3d letters at the top center
- The letters should not be round.
- The Morvanix letters should be in neon green like color Or another option is a color blend that has green in it
- the Color of the letters is not the same as previous album covers
- The letters are similar to the Savage Drommel comic book letters but not the same as those
- The song tittle should at the bottom in a cursive style font and in flame like colors
- I attached examples of the cursive style font and the neon style
- The name of the song is Noche Serena
Hi everyone, I'm getting some really good designs in this contest! You are all great artists and designers.
A couple of things to consider:
- The song is sung in Spanish by a female singer
-The song is about dancing to reggae, dancehall, salsa and cumbia
- The song is also about attraction in the dance. Attraction to the music itself and also attraction to each other (Romantic, Passionate)
-The name of the song Noche Serena means Hot Dance/ Hot Dancing
-The style of the song is a mix of dancehall(modern reggae style) and reggaeton.
-The style of the people dancing is meant more of a club or dance vibe not so much of a rave.
-The Dj is not the most important aspect but just something to go along with people dancing.
Hopefully this helps any artists understand the mood/concept of the cover I'm looking for. Any questions/suggestions/ concepts feel free to direct message me. I might also have another contest soon for another album cover after this contest ends.
Thank you & Bless Up,
-Tomás

```html
<!DOCTYPE html>
<html lang="es">
<head>
<meta charset="UTF-8">
<title>Morvanix – Noche Serena</title>
<link rel="stylesheet" href="https://fonts.googleapis.com/css2?family=Bungee&family=Lobster&family=Yellowtail&display=block">
<style>
  :root {
    --neon-green: #1cff1c;
    --deep-green: #0a7a10;
    --ink-navy: #1d0a6b;
    --spray-blue: #1f22ff;
    --spray-magenta: #ff2bd6;
    --spray-teal: #2a8c9c;
    --club-violet: #5b3fa8;
    --flame-yellow: #ffe21a;
    --flame-amber: #ffb000;
    --flame-orange: #ff6a00;
    --flame-red: #9a1a00;
    --crowd-black: #050308;
    --crowd-navy: #13204a;
  }

  html, body {
    margin: 0;
    padding: 0;
    width: 1200px;
    height: 1200px;
    overflow: hidden;
    background: #000;
  }

  .cover {
    position: relative;
    width: 1200px;
    height: 1200px;
    overflow: hidden;
    background:
      radial-gradient(ellipse 44% 30% at 52% 22%, rgba(28,255,28,0.98) 0%, rgba(28,255,28,0.8) 55%, rgba(28,255,28,0) 100%),
      radial-gradient(ellipse 22% 26% at 50% 52%, rgba(28,235,50,0.9) 0%, rgba(28,235,50,0) 100%),
      radial-gradient(ellipse 30% 22% at 90% 8%, var(--spray-magenta) 0%, rgba(255,43,214,0) 100%),
      radial-gradient(ellipse 22% 26% at 7% 36%, var(--spray-magenta) 0%, rgba(255,43,214,0) 100%),
      radial-gradient(ellipse 26% 26% at 3% 3%, var(--spray-blue) 0%, rgba(31,34,255,0) 100%),
      radial-gradient(ellipse 28% 36% at 97% 46%, var(--spray-blue) 0%, rgba(31,34,255,0) 100%),
      linear-gradient(180deg, #3b2cc8 0%, #2f50c8 45%, var(--spray-teal) 75%, var(--club-violet) 100%);
  }

  .crowd {
    position: absolute;
    left: 0;
    right: 0;
    top: 440px;
    bottom: 0;
    background:
      radial-gradient(ellipse 14% 26% at 50% 30%, rgba(20,90,60,0.55) 0%, rgba(20,90,60,0) 100%),
      radial-gradient(ellipse 18% 48% at 10% 70%, rgba(5,3,8,0.95) 0%, rgba(5,3,8,0) 100%),
      radial-gradient(ellipse 16% 52% at 30% 68%, rgba(5,3,8,0.95) 0%, rgba(5,3,8,0) 100%),
      radial-gradient(ellipse 18% 56% at 54% 66%, rgba(5,3,8,0.97) 0%, rgba(5,3,8,0) 100%),
      radial-gradient(ellipse 17% 54% at 77% 66%, rgba(5,3,8,0.97) 0%, rgba(5,3,8,0) 100%),
      radial-gradient(ellipse 12% 44% at 95% 74%, rgba(5,3,8,0.9) 0%, rgba(5,3,8,0) 100%),
      linear-gradient(180deg, rgba(19,32,74,0) 0%, rgba(19,32,74,0.45) 35%, rgba(19,32,74,0.6) 100%);
  }

  .artist-name {
    position: absolute;
    top: 100px;
    left: 0;
    right: 0;
    margin: 0;
    text-align: center;
    font-family: "Bungee", "Arial Black", sans-serif;
    font-weight: 400;
    font-size: 172px;
    line-height: 1;
    letter-spacing: 2px;
    color: var(--neon-green);
    -webkit-text-stroke: 3px var(--ink-navy);
    transform: scaleY(1.4);
    transform-origin: 50% 0;
    text-shadow:
      -2px 2px 0 var(--deep-green),
      -4px 4px 0 var(--deep-green),
      -6px 6px 0 var(--deep-green),
      -8px 8px 0 var(--deep-green),
      -10px 10px 0 var(--deep-green),
      -12px 12px 0 var(--deep-green),
      -14px 14px 0 var(--deep-green),
      -16px 16px 0 var(--deep-green),
      -18px 18px 0 var(--deep-green),
      -20px 20px 0 var(--deep-green),
      -22px 22px 0 var(--ink-navy),
      -24px 24px 0 var(--ink-navy),
      0 0 30px rgba(28,255,28,0.75);
  }

  .song-title {
    position: absolute;
    top: 860px;
    left: 0;
    right: 0;
    margin: 0;
    text-align: center;
    font-family: "Yellowtail", "Lobster", cursive;
    font-weight: 400;
    font-size: 200px;
    line-height: 1.2;
    white-space: nowrap;
    filter: drop-shadow(5px 7px 0 var(--flame-red)) drop-shadow(0 0 8px rgba(0,0,0,0.55));
  }

  .song-title span {
    background: linear-gradient(180deg, var(--flame-yellow) 22%, var(--flame-amber) 55%, var(--flame-orange) 88%);
    -webkit-background-clip: text;
    background-clip: text;
    color: transparent;
    padding: 0 30px;
  }
</style>
</head>
<body>
  <main class="cover">
    <div class="crowd" role="img" aria-label="Black silhouettes of people dancing in a club with raised arms, with a DJ in headphones behind them in the green light"></div>

    <h1 class="artist-name">MORVANIX</h1>
    <h2 class="song-title"><span>Noche Serena</span></h2>
  </main>
</body>
</html>
```